Thornvale Group needs a business card design

We need a new business card design using the logo recently selected in a logo competition on Pixel Bazaar. Our business is a consultancy specializing in aviation and energy and the winning business card design will promote an image of precision and professionalism with creativity.

Please use the logo with the name on the front of the card and use a complementary font. Make the back white with either the light grey or dark grey logo.

Target Market(s)

Senior finance and legal leaders at aviation and energy companies

Industry/Entity Type

Management Consulting

Contact Information for Business Card

Peter Castrell
President
Thornvale Group

www.thornvalegroup.example

(555) 204-6391
pc@thornvalegroup.example

Requirements
Must have
• Professional font that goes well with the logo font

```html
<!DOCTYPE html>
<html lang="en">
<head>
<meta charset="utf-8">
<title>Thornvale Group – Business Card</title>
<link rel="stylesheet" href="https://fonts.googleapis.com/css2?family=Open+Sans:wght@400;600;700&display=swap">
<style>
  :root {
    --navy: #123f73;
    --ink-grey: #555a60;
    --card-white: #ffffff;
    --panel-white: #f7f9fb;
    --backdrop: #e4e5e7;
    --card-edge: #d3d6da;
  }
  * { box-sizing: border-box; margin: 0; padding: 0; }
  html, body {
    width: 1200px;
    height: 900px;
    overflow: hidden;
  }
  body {
    background: var(--backdrop);
    font-family: "Open Sans", Arial, sans-serif;
    position: relative;
  }
  .card {
    position: absolute;
    left: 320px;
    width: 560px;
    height: 320px;
    background: var(--card-white);
    border: 1px solid var(--card-edge);
    overflow: hidden;
  }
  .card--back { top: 100px; }
  .card--front { top: 480px; }

  /* Back: company side */
  .tagline {
    position: absolute;
    top: 34px;
    left: 0;
    right: 0;
    text-align: center;
    color: var(--navy);
    font-weight: 700;
    font-size: 14px;
  }
  .brand-panel {
    position: absolute;
    top: 68px;
    left: 160px;
    width: 240px;
    height: 170px;
    background: var(--panel-white);
    display: flex;
    align-items: center;
    justify-content: center;
    gap: 10px;
  }
  .brand-square {
    width: 16px;
    height: 16px;
    background: var(--navy);
  }
  .brand-name {
    color: var(--navy);
    font-weight: 600;
    font-size: 24px;
    letter-spacing: 0.5px;
  }
  .sectors {
    position: absolute;
    top: 256px;
    left: 0;
    right: 0;
    text-align: center;
    color: var(--ink-grey);
    font-weight: 700;
    font-size: 15px;
  }

  /* Front: contact side */
  .accent-band {
    position: absolute;
    top: 0;
    left: 0;
    width: 120px;
    height: 100%;
    background: var(--navy);
  }
  .person {
    position: absolute;
    top: 58px;
    right: 42px;
    text-align: right;
  }
  .person-name {
    color: var(--navy);
    font-weight: 700;
    font-size: 20px;
  }
  .person-role {
    color: var(--ink-grey);
    font-size: 15px;
    margin-top: 2px;
  }
  .contact {
    position: absolute;
    bottom: 40px;
    right: 36px;
    list-style: none;
    color: var(--ink-grey);
    font-size: 16px;
  }
  .contact-item {
    display: flex;
    align-items: center;
    justify-content: flex-end;
    gap: 12px;
    line-height: 26px;
  }
  .contact-icon { width: 14px; height: 14px; fill: var(--navy); }
</style>
</head>
<body>
  <section class="card card--back" aria-label="Business card, company side">
    <p class="tagline">Finance and Strategy Consulting</p>
    <div class="brand-panel">
      <span class="brand-square"></span>
      <span class="brand-name">Thornvale Group</span>
    </div>
    <p class="sectors">Aviation - Manufacturing - Energy</p>
  </section>

  <section class="card card--front" aria-label="Business card, contact side">
    <div class="accent-band"></div>
    <div class="person">
      <p class="person-name">Peter J. Castrell</p>
      <p class="person-role">President</p>
    </div>
    <ul class="contact">
      <li class="contact-item">
        <span>(555) 204-6391</span>
        <svg class="contact-icon" viewBox="0 0 14 14" aria-hidden="true">
          <path d="M1 4 Q7 0 13 4 L11 6 L9 5 L9 4 Q7 3 5 4 L5 5 L3 6 Z"/>
          <rect x="3" y="7" width="8" height="6" rx="1"/>
        </svg>
      </li>
      <li class="contact-item">
        <span>pc@thornvalegroup.example</span>
        <svg class="contact-icon" viewBox="0 0 14 14" aria-hidden="true">
          <path d="M1 3 H13 V11 H1 Z M1.8 3.8 L7 8 L12.2 3.8" fill="var(--navy)" stroke="#ffffff" stroke-width="0.9"/>
        </svg>
      </li>
    </ul>
  </section>
</body>
</html>
```